Commercial Loan Originator Business Card (CHANGE COLORS SCHEME)

CHANGE COLOR SCHEME - SAME DESIGN

Name Marlene Agate
Title Commercial Loan Originator
Office (800) 417-2906 x68
Direct (240) 615-2043
Email freshgreens4life@quillbox.example

Name Dale Morrow
Office (800) 417-2906 x70
Direct (410) 392-5184
Email d.morthehomeguy@quillbox.example

Name Leonard Vasko
Office (800) 417-2906 x71
Direct (215) 463-0712
Email l.vasko41@quillbox.example

Name Gwen Halsey
Office (800) 417-2906 x
Direct (202) 548-1370
Email ghalsey63@quillbox.example

Name Mirna Ashby
Office (800) 417-2906 x72
Direct (240) 871-4526
Email tristatehomelending@quillbox.example

```html
<!DOCTYPE html>
<html lang="en">
<head>
<meta charset="utf-8">
<title>Gwen Halsey — Business Card</title>
<link href="https://fonts.googleapis.com/css2?family=Playfair+Display:wght@400;500&family=Poppins:wght@300;400&display=swap" rel="stylesheet">
<style>
  :root {
    --stage: #979797;
    --card: #ffffff;
    --card-sheen: #f1f2f4;
    --band-light: #8ec3ff;
    --band-mid: #1f56c8;
    --band-deep: #02127a;
    --name-top: #2d62c9;
    --name-bottom: #0a2585;
    --gold: #d6a23a;
    --gold-light: #efc46a;
    --gold-deep: #c48a22;
    --ink: #1b1b1f;
  }
  * { box-sizing: border-box; margin: 0; padding: 0; }
  html, body { width: 1200px; height: 1196px; overflow: hidden; }
  body { background: var(--stage); position: relative; font-family: "Poppins", sans-serif; }

  .card {
    position: absolute; left: 180px; width: 840px; height: 480px;
    background: linear-gradient(125deg, var(--card) 0%, var(--card) 55%, var(--card-sheen) 70%, var(--card) 78%, var(--card-sheen) 92%, var(--card) 100%);
    box-shadow: 18px 14px 22px rgba(0,0,0,.35);
    overflow: hidden;
  }
  .card--front { top: 74px; }
  .card--back { top: 594px; }

  .side-band {
    position: absolute; left: 0; top: 0; width: 112px; height: 100%;
    background: linear-gradient(180deg, var(--band-light) 0%, var(--band-mid) 45%, var(--band-deep) 100%);
  }

  .name {
    font-family: "Playfair Display", serif; font-weight: 400;
    text-transform: uppercase; letter-spacing: 1px; line-height: 1;
    background: linear-gradient(180deg, var(--name-top), var(--name-bottom));
    -webkit-background-clip: text; background-clip: text; color: transparent;
  }

  /* front */
  .portrait-frame {
    position: absolute; left: 130px; top: 74px; width: 324px; height: 335px;
    border: 2px solid var(--gold);
  }
  .portrait {
    position: absolute; left: 46px; top: 83px; width: 396px; height: 314px;
    border: 3px solid #fff;
    background: linear-gradient(110deg, #6f9a5a 0%, #5a4a42 30%, #8a5a44 55%, #c47d70 80%, #9c8f8c 100%);
  }
  .card--front .name { position: absolute; left: 484px; font-size: 74px; }
  .card--front .name--first { top: 138px; }
  .card--front .name--last { top: 208px; }
  .rule { position: absolute; left: 485px; top: 285px; width: 156px; height: 2px; background: var(--gold); }
  .job-title {
    position: absolute; left: 485px; top: 300px; width: 220px;
    font-size: 17px; line-height: 23px; color: var(--ink); letter-spacing: .3px;
  }

  /* back */
  .name-frame {
    position: absolute; left: 186px; top: 66px; width: 506px; height: 112px;
    border: 2px solid var(--gold);
  }
  .name-line {
    position: absolute; left: 198px; height: 68px; padding: 0 10px 0 12px;
    background: var(--card); overflow: visible; white-space: nowrap;
  }
  .name-line--first { top: 41px; }
  .name-line--last { top: 125px; }
  .name-line .name { display: block; font-size: 85px; line-height: 68px; }

  .contacts { position: absolute; left: 187px; top: 240px; list-style: none; }
  .contact { display: flex; align-items: center; height: 46px; margin-bottom: 12px; }
  .contact__icon {
    width: 45px; height: 45px; border-radius: 50%; flex: none;
    background: radial-gradient(circle at 35% 30%, var(--gold-light), var(--gold) 55%, var(--gold-deep));
    display: flex; align-items: center; justify-content: center;
  }
  .contact__text { margin-left: 16px; font-size: 30px; font-weight: 300; color: var(--ink); letter-spacing: .2px; }
  .contact--email .contact__text { margin-left: 20px; }
</style>
</head>
<body>

<section class="card card--front" aria-label="Card front">
  <div class="side-band"></div>
  <div class="portrait-frame"></div>
  <div class="portrait" role="img" aria-label="Portrait photo of Gwen Halsey"></div>
  <h1 class="name name--first">Gwen</h1>
  <h1 class="name name--last">Halsey</h1>
  <div class="rule"></div>
  <p class="job-title">Commercial Loan Originator</p>
</section>

<section class="card card--back" aria-label="Card back">
  <div class="side-band"></div>
  <div class="name-frame"></div>
  <div class="name-line name-line--first"><span class="name">Gwen</span></div>
  <div class="name-line name-line--last"><span class="name">Halsey</span></div>
  <ul class="contacts">
    <li class="contact contact--office">
      <span class="contact__icon">
        <svg width="24" height="20" viewBox="0 0 24 20" fill="#fff"><path d="M2 7c0-4 20-4 20 0v2h-5V7H7v2H2z"/><path d="M6 10h12l3 9H3z"/><rect x="9" y="12" width="6" height="5" fill="#d6a23a"/></svg>
      </span>
      <span class="contact__text">(800) 417-2906 x</span>
    </li>
    <li class="contact contact--direct">
      <span class="contact__icon">
        <svg width="24" height="24" viewBox="0 0 24 24" fill="none" stroke="#fff" stroke-width="2.2" stroke-linecap="round"><path d="M6 3l3 4-2 2c1 3 4 6 7 7l2-2 4 3-2 3C10 20 4 14 3 6z" fill="#fff"/><path d="M14 6a4 4 0 0 1 4 4M14 2a8 8 0 0 1 8 8"/></svg>
      </span>
      <span class="contact__text">(202) 548-1370</span>
    </li>
    <li class="contact contact--email">
      <span class="contact__icon">
        <svg width="26" height="18" viewBox="0 0 26 18" fill="none" stroke="#fff" stroke-width="1.6"><rect x="1" y="1" width="24" height="16"/><path d="M1 1l12 10L25 1M1 17l9-8M25 17l-9-8"/></svg>
      </span>
      <span class="contact__text">ghalsey63@quillbox.example</span>
    </li>
  </ul>
</section>

</body>
</html>
```